Mindfulness School for Children -- Business Cards

We're looking for business cards for our school directors and owners. We're a mindfulness school for children called little lanterns. Attached are our logos/icons.

```html
<!DOCTYPE html>
<html lang="en">
<head>
<meta charset="utf-8">
<title>little lanterns — business cards</title>
<link rel="stylesheet" href="https://fonts.googleapis.com/css2?family=Montserrat:wght@400;500;600&display=swap">
<style>
  :root {
    --stage: #1f1f1f;
    --white: #ffffff;
    --teal: #549f8e;
    --teal-deep: #4e9886;
    --mint: #96cfa2;
    --sky: #7cc3dc;
    --ink: #2b2b2b;
    --brand: #5fa896;
  }
  * { box-sizing: border-box; margin: 0; padding: 0; }
  html, body {
    width: 1200px; height: 1015px; overflow: hidden;
    background: var(--stage);
    font-family: "Montserrat", sans-serif;
  }
  .sheet {
    position: relative; width: 1200px; height: 1015px;
    display: flex; flex-direction: column; align-items: center;
    justify-content: center; gap: 48px;
  }
  .card {
    position: relative; width: 760px; height: 434px; overflow: hidden;
    box-shadow: 0 18px 40px rgba(0,0,0,.55);
  }

  /* front */
  .card--front { display: flex; align-items: center; justify-content: center; }
  .card__texture {
    position: absolute; inset: 0;
    background:
      radial-gradient(ellipse at 25% 35%, rgba(150,206,168,.9), transparent 55%),
      radial-gradient(ellipse at 70% 70%, rgba(150,206,168,.8), transparent 50%),
      radial-gradient(ellipse at 80% 25%, rgba(88,165,145,.9), transparent 50%),
      linear-gradient(135deg, #7cc0a4, #68ae98 50%, #83c6a6);
  }
  .wordmark {
    position: relative; display: flex; align-items: center; gap: 14px;
    font-weight: 500; letter-spacing: .5px; white-space: nowrap;
  }
  .wordmark__dot { width: 16px; height: 16px; border-radius: 50%; flex: none; }
  .card--front .wordmark { color: var(--white); font-size: 56px; }
  .card--front .wordmark__dot { background: var(--white); }

  /* back */
  .card--back { background: var(--white); }
  .card--back .wordmark {
    position: absolute; left: 0; right: 0; top: 88px; justify-content: center;
    color: var(--brand); font-size: 50px;
  }
  .card--back .wordmark__dot { background: var(--brand); }
  .info-band {
    position: absolute; left: 0; right: 0; top: 236px; height: 98px;
    display: flex;
    background: linear-gradient(90deg, var(--teal) 0%, var(--teal-deep) 45%, var(--mint) 100%);
    border-top: 4px solid var(--sky); border-bottom: 4px solid var(--sky);
  }
  .person {
    width: 330px; padding-left: 120px; display: flex; flex-direction: column;
    justify-content: center; color: var(--white);
    border-right: 1px solid rgba(255,255,255,.55);
  }
  .person__name { font-size: 27px; font-weight: 600; white-space: nowrap; }
  .person__role { font-size: 14px; font-weight: 400; margin-top: 2px; }
  .contacts {
    list-style: none; padding-left: 26px; display: flex; flex-direction: column;
    justify-content: center; gap: 5px; color: var(--white); font-size: 14px;
  }
  .contacts li { display: flex; align-items: center; gap: 8px; white-space: nowrap; }
  .contacts svg { width: 14px; height: 14px; fill: none; stroke: var(--white); stroke-width: 1.6; flex: none; }
  .address {
    position: absolute; left: 0; right: 0; top: 370px; text-align: center;
    color: var(--ink); font-size: 16px; font-weight: 500;
  }
</style>
</head>
<body>
<main class="sheet">
  <section class="card card--front">
    <div class="card__texture" role="img" aria-label="Soft cloudy mint and teal watercolour texture"></div>
    <div class="wordmark"><span class="wordmark__dot"></span>little lanterns</div>
  </section>

  <section class="card card--back">
    <div class="wordmark"><span class="wordmark__dot"></span>little lanterns</div>
    <div class="info-band">
      <div class="person">
        <span class="person__name">Daniel Reeves</span>
        <span class="person__role">Managing Director</span>
      </div>
      <ul class="contacts">
        <li><svg viewBox="0 0 16 16"><path d="M4 2l2.5 3-1.5 1.5a8 8 0 0 0 4.5 4.5L11 9.5l3 2.5-1.5 2C7 14 2 9 2 3.5z"/></svg>071-555 210 347</li>
        <li><svg viewBox="0 0 16 16"><rect x="1.5" y="3.5" width="13" height="9"/><path d="M1.5 3.5L8 9l6.5-5.5"/></svg>hello@lanternsmail.com</li>
        <li><svg viewBox="0 0 16 16"><circle cx="8" cy="8" r="6.5"/><path d="M1.5 8h13M8 1.5c-3 3.5-3 9.5 0 13M8 1.5c3 3.5 3 9.5 0 13"/></svg>www.lanternschool.com</li>
      </ul>
    </div>
    <p class="address">18, Willow Lane, Brookfield 30817, Eastmoor</p>
  </section>
</main>
</body>
</html>
```